physical therapy flyer

2 office locations speciality programs - work injury / Motor vehicle accidents - spanish speaking - do not put balance defecits/ fall prevention - Spanish speaking
neck and back pain shoulder pain/ rotator cuff disorder / bursitis
hip pain knee andle and foot pain post operative care including Spine , shoulder , knee , total joint replacement

Meadowlark Physical therapy & Chiropractic
4871 Pinecrest BLvd
dalton heights ny 10592
7185820147
3715 Tillman Parkway
Fernvale NY 10592
7189043218
www.meadowlarkptrehab.com

```html
<!DOCTYPE html>
<html lang="en">
<head>
<meta charset="utf-8">
<title>Meadowlark Physical Therapy &amp; Chiropractic – Flyer</title>
<link href="https://fonts.googleapis.com/css2?family=Poppins:wght@300;400;500;600;700;800&display=swap" rel="stylesheet">
<style>
  :root{
    --backdrop:#7a7a7a;
    --wood:#2b221d;
    --wood-line:#362b25;
    --green:#3d9b48;
    --green-dark:#2f8a3d;
    --green-light:#6fd46c;
    --ink:#161616;
    --paper:#ffffff;
    --red:#e3141b;
    --yellow:#ffe600;
    --photo-light:#e9e6e2;
    --photo-skin:#c9a48c;
  }
  *{margin:0;padding:0;box-sizing:border-box}
  html,body{width:899px;height:1200px;overflow:hidden;background:var(--backdrop)}
  body{font-family:'Poppins',sans-serif;color:var(--ink)}
  .stage{position:absolute;left:0;top:0;width:1500px;height:2000px;transform:scale(0.59933);transform-origin:0 0}
  .flyer{position:absolute;left:123px;top:189px;width:1255px;height:1623px;background:var(--paper);overflow:hidden}
  .abs{position:absolute}

  .hero-band{left:0;top:0;width:1255px;height:534px;
    background:repeating-linear-gradient(90deg,var(--wood) 0 7px,var(--wood-line) 7px 9px,var(--wood) 9px 19px)}
  .footer-band{left:0;top:1487px;width:1255px;height:136px;
    background:repeating-linear-gradient(90deg,var(--wood) 0 7px,var(--wood-line) 7px 9px,var(--wood) 9px 19px);
    display:flex;align-items:center;padding-left:88px;gap:14px}

  .tile{position:absolute}
  .tile--green{background:linear-gradient(135deg,#7ade74,#53c24f)}
  .tile--light{background:linear-gradient(135deg,#f2efec,#d9d3cc)}
  .tile--coat{background:linear-gradient(160deg,#e8e4e0,#f7f5f3 55%,#cfc6bd)}

  .brand{left:75px;top:112px;display:flex;align-items:center;gap:14px;color:#fff;font-weight:300;font-size:20px;line-height:24px}
  .brand__dot{width:18px;height:18px;border-radius:50%;background:#fff;flex:none}

  .eyebrow{left:75px;top:220px;color:#fff;font-size:44px;font-weight:400;letter-spacing:18px}
  .headline{left:75px;top:278px;color:var(--green);font-size:68px;font-weight:800;line-height:70px;letter-spacing:-1px}
  .cta{left:77px;top:509px;width:560px;height:66px;background:var(--green);border:3px solid #fff;
    box-shadow:0 3px 0 #d8d8d8;color:#fff;font-size:34px;font-weight:700;display:flex;align-items:center;justify-content:center}

  .section-title{left:75px;top:600px;font-size:40px;font-weight:400;line-height:50px}
  .section-title b{font-weight:700}
  .section-rule{left:537px;top:638px;width:645px;height:2px;background:#333}

  .program{position:absolute;left:75px;display:flex;align-items:center;gap:20px;font-size:30px;font-weight:600;line-height:35px}
  .badge-icon{width:82px;height:82px;border-radius:50%;border:2px dashed #555;display:flex;align-items:center;justify-content:center;flex:none}
  .badge-icon span{width:70px;height:70px;border-radius:50%;background:var(--green);display:block}
  .divider{position:absolute;left:0;width:640px;height:3px;background:linear-gradient(90deg,transparent,#d6d6d6 20%,#d6d6d6 80%,transparent)}

  .tick-list{position:absolute;list-style:none;font-size:28px;line-height:33px}
  .tick-list li{position:relative;padding-left:28px;margin-bottom:6px}
  .tick-list li::before{content:"";position:absolute;left:0;top:9px;width:16px;height:16px;border-radius:50%;background:var(--green)}
  .tick-list li::after{content:"";position:absolute;left:5px;top:12px;width:4px;height:7px;border:solid #fff;border-width:0 2px 2px 0;transform:rotate(45deg)}

  .photo{position:absolute;width:248px;height:248px}
  .photo--clinic{background:linear-gradient(150deg,#d9b8a2,#f0ebe6 45%,#28324a)}
  .photo--green-a{background:linear-gradient(160deg,#8de786,#5bc957)}
  .photo--green-b{background:linear-gradient(160deg,#5bc957,#2f6d34);border-bottom-left-radius:22px}
  .photo--studio{background:linear-gradient(160deg,#f4f4f4,#e4d8cf 50%,#b9c6cf);border-bottom-right-radius:22px}

  .seal{left:962px;top:896px;width:240px;height:240px}
  .seal__text{position:absolute;inset:0;display:flex;flex-direction:column;align-items:center;justify-content:center;text-align:center}
  .seal__big{color:var(--yellow);font-size:36px;font-weight:800;line-height:40px}
  .seal__small{color:#fff;font-size:22px;line-height:24px}

  .locations-title{left:72px;top:1220px;color:var(--green);font-size:30px;font-weight:700;letter-spacing:4px}
  .address{position:absolute;left:78px;display:flex;align-items:center;gap:8px;font-size:22px;font-weight:400}
  .phone{position:absolute;left:74px;display:flex;align-items:center;gap:6px;font-size:30px;font-weight:700}
  .loc-rule{left:74px;top:1366px;width:522px;height:1.5px;background:#333}

  .footer-label{color:var(--green);font-size:46px;font-weight:700}
  .footer-url{color:#fff;font-size:48px;font-weight:400;letter-spacing:4px}
  .footer-url b{font-weight:700}
</style>
</head>
<body>
<div class="stage">
  <div class="flyer">
    <div class="abs hero-band"></div>

    <div class="tile tile--green" style="left:784px;top:52px;width:85px;height:85px" role="img" aria-label="Close-up of a spine model"></div>
    <div class="tile tile--light" style="left:657px;top:146px;width:212px;height:212px" role="img" aria-label="Hands holding a spine model"></div>
    <div class="tile tile--coat" style="left:877px;top:0;width:378px;height:358px" role="img" aria-label="Clinician in a white coat with stethoscope"></div>
    <div class="tile tile--green" style="left:657px;top:367px;width:212px;height:212px;border-bottom-left-radius:22px" role="img" aria-label="Pelvis and lower spine model"></div>
    <div class="tile tile--light" style="left:877px;top:367px;width:212px;height:212px" role="img" aria-label="Clinician's arm and hip joint model"></div>
    <div class="tile tile--green" style="left:1097px;top:367px;width:158px;height:212px" role="img" aria-label="Clinician's coat, green toned"></div>

    <div class="abs brand">
      <span class="brand__dot"></span>
      <span>Meadowlark Physical Therapy,<br>Chiropractic, and Acupuncture</span>
    </div>

    <div class="abs eyebrow">MEADOWLARK</div>
    <h1 class="abs headline">PHYSICAL<br>THERAPY &amp;<br>CHIROPRACTIC</h1>
    <div class="abs cta">Two Convenient Locations!</div>

    <h2 class="abs section-title">SPECIALTY <b>PROGRAMS</b></h2>
    <div class="abs section-rule"></div>

    <div class="program" style="top:680px"><span class="badge-icon"><span></span></span>Work Injuries</div>
    <div class="divider" style="top:770px"></div>
    <div class="program" style="top:780px"><span class="badge-icon"><span></span></span>Motor Vehicle Accidents</div>
    <div class="divider" style="top:868px"></div>
    <div class="program" style="top:878px"><span class="badge-icon"><span></span></span>Neck &amp; Back Pain</div>
    <div class="divider" style="top:966px"></div>
    <div class="program" style="top:975px"><span class="badge-icon"><span></span></span>Shoulder Pain, Rotator<br>Cuff Injuries, Bursitis</div>
    <div class="divider" style="top:1066px"></div>
    <div class="program" style="top:1080px"><span class="badge-icon"><span></span></span>Hip, Knee, Ankle, and<br>Foot Pain</div>

    <div class="program" style="left:649px;top:673px"><span class="badge-icon"><span></span></span>Post-Operative Care</div>
    <ul class="tick-list" style="left:653px;top:772px">
      <li>Total Joint<br>Replacement</li>
      <li>Neck &amp;</li>
      <li>Back Pain</li>
    </ul>
    <ul class="tick-list" style="left:948px;top:772px">
      <li>Spine</li>
      <li>Shoulder</li>
      <li>Knee</li>
    </ul>

    <div class="photo photo--clinic" style="left:661px;top:954px" role="img" aria-label="Therapist stretching a patient's leg"></div>
    <div class="photo photo--green-a" style="left:923px;top:954px" role="img" aria-label="Therapist treating a patient's shoulder, green toned"></div>
    <div class="photo photo--green-b" style="left:661px;top:1216px" role="img" aria-label="Therapist assisting an older patient with back pain, green toned"></div>
    <div class="photo photo--studio" style="left:923px;top:1216px" role="img" aria-label="Woman seated in a therapy room during a shoulder assessment"></div>

    <div class="abs seal">
      <svg width="240" height="240" viewBox="0 0 240 240">
        <circle cx="120" cy="120" r="106" fill="var(--red)"/>
        <circle cx="120" cy="120" r="110" fill="none" stroke="var(--red)" stroke-width="16" stroke-dasharray="14 7"/>
        <circle cx="120" cy="120" r="106" fill="none" stroke="#fff" stroke-width="2" opacity=".35"/>
      </svg>
      <div class="seal__text">
        <span class="seal__big">SPANISH<br>SPEAKING</span>
        <span class="seal__small" style="font-weight:700;margin-top:4px">SERVICES</span>
        <span class="seal__small">AVAILABLE</span>
      </div>
    </div>

    <h3 class="abs locations-title">LOCATIONS</h3>

    <div class="address" style="top:1282px">
      <svg width="20" height="24" viewBox="0 0 20 24"><path d="M10 1a7 7 0 0 0-7 7c0 5 7 12 7 12s7-7 7-12a7 7 0 0 0-7-7z" fill="var(--green)"/><circle cx="10" cy="8" r="2.6" fill="#fff"/><ellipse cx="10" cy="22" rx="8" ry="1.8" fill="none" stroke="var(--green)" stroke-width="1.6"/></svg>
      4871 Pinecrest Blvd, Dalton Heights, NY 10592
    </div>
    <div class="phone" style="top:1310px">
      <svg width="26" height="26" viewBox="0 0 26 26"><circle cx="13" cy="13" r="12" fill="var(--green)"/><path d="M8.5 7.5l2.5-.5 1.3 3-1.6 1.2a8 8 0 0 0 3.6 3.6l1.2-1.6 3 1.3-.5 2.5c-5.5.4-9.9-4-9.5-9.5z" fill="#fff"/></svg>
      718-582-0147
    </div>
    <div class="abs loc-rule"></div>
    <div class="address" style="top:1386px">
      <svg width="20" height="24" viewBox="0 0 20 24"><path d="M10 1a7 7 0 0 0-7 7c0 5 7 12 7 12s7-7 7-12a7 7 0 0 0-7-7z" fill="var(--green)"/><circle cx="10" cy="8" r="2.6" fill="#fff"/><ellipse cx="10" cy="22" rx="8" ry="1.8" fill="none" stroke="var(--green)" stroke-width="1.6"/></svg>
      3715 Tillman Parkway, Fernvale, NY 10592
    </div>
    <div class="phone" style="top:1414px">
      <svg width="26" height="26" viewBox="0 0 26 26"><circle cx="13" cy="13" r="12" fill="var(--green)"/><path d="M8.5 7.5l2.5-.5 1.3 3-1.6 1.2a8 8 0 0 0 3.6 3.6l1.2-1.6 3 1.3-.5 2.5c-5.5.4-9.9-4-9.5-9.5z" fill="#fff"/></svg>
      718-904-3218
    </div>

    <div class="abs footer-band">
      <span class="footer-label">Visit us at:</span>
      <span class="footer-url">www.<b>meadowlarkptrehab</b>.com</span>
    </div>
  </div>
</div>
</body>
</html>
```